Marwick Law Letterhead

We need a new letterhead design for a Law Firm. The address for the law firm is 1475 Calloway Street, Suite 210, Houston, Texas 77041. Phone Number: 832-361-9027; Fax Number: 832-614-7359. The logo is uploaded to the project.

```html
<!DOCTYPE html>
<html lang="en">
<head>
<meta charset="utf-8">
<title>Marwick Law Letterhead</title>
<link href="https://fonts.googleapis.com/css2?family=Montserrat:wght@300;400;500&family=Tinos&display=swap" rel="stylesheet">
<style>
  :root {
    --navy: #1b3466;
    --navy-deep: #12264d;
    --red: #d5262b;
    --text: #8a8a8a;
    --text-dark: #333333;
    --backdrop: #d4d5d7;
    --paper: #ffffff;
  }
  * { margin: 0; padding: 0; box-sizing: border-box; }
  html, body { width: 1200px; height: 1200px; overflow: hidden; background: var(--backdrop); }
  .letterhead {
    position: absolute; left: 190px; top: 20px; width: 820px; height: 1160px;
    background: var(--paper); font-family: "Montserrat", sans-serif; font-weight: 300; color: var(--text);
  }
  .header-band {
    position: absolute; left: 0; top: 0; width: 820px; height: 46px;
    background: linear-gradient(90deg, var(--navy), var(--navy-deep));
  }
  .header-rule {
    position: absolute; left: 0; top: 52px; width: 820px; height: 4px; background: var(--red);
  }
  .firm-name {
    position: absolute; left: 72px; top: 116px;
    font-family: "Tinos", serif; font-size: 34px; color: var(--navy); letter-spacing: 0.5px;
    display: flex; align-items: center; gap: 12px;
  }
  .firm-mark { width: 44px; height: 44px; background: var(--navy); }
  .recipient { position: absolute; left: 83px; top: 264px; font-size: 11.5px; line-height: 18px; }
  .recipient .label { font-size: 14px; font-weight: 400; letter-spacing: 2px; color: var(--text-dark); margin-bottom: 4px; }
  .recipient .name { font-size: 14px; font-weight: 400; color: var(--red); margin-bottom: 4px; }
  .date { position: absolute; right: 83px; top: 264px; font-size: 11.5px; font-weight: 400; color: var(--text-dark); }
  .body-copy {
    position: absolute; left: 83px; top: 414px; width: 655px;
    font-size: 12.2px; line-height: 14.6px; letter-spacing: -0.25px; text-align: justify;
  }
  .body-copy p { margin-bottom: 14.5px; }
  .signature { position: absolute; left: 83px; top: 818px; width: 140px; height: 36px; background: linear-gradient(90deg, #e9e9e9, #f6f6f6); }
  .signatory { position: absolute; left: 81px; top: 864px; }
  .signatory .name { font-size: 13.5px; font-weight: 400; color: var(--text-dark); }
  .signatory .title { font-size: 11px; margin-top: 2px; }
  .footer { position: absolute; left: 0; top: 1094px; width: 820px; text-align: center; font-family: "Tinos", serif; color: var(--navy); font-size: 14px; }
  .footer .contacts { display: inline-flex; align-items: center; gap: 6px; }
  .footer .contacts svg { width: 12px; height: 12px; }
  .footer .rule { width: 320px; height: 1px; background: var(--navy); margin: 5px auto 6px; }
</style>
</head>
<body>
<main class="letterhead">
  <div class="header-band" aria-hidden="true"></div>
  <div class="header-rule" aria-hidden="true"></div>

  <div class="firm-name"><span class="firm-mark"></span>Marwick Law</div>

  <section class="recipient">
    <div class="label">TO</div>
    <div class="name">Daniel Pretorius</div>
    <div>Human Resources</div>
    <div>Northfield Inc.</div>
    <div>2210-B Lindell Road, Carver</div>
    <div>E41 USA</div>
  </section>
  <div class="date">Friday, 01/01/2018</div>

  <article class="body-copy">
    <p>Lorem ipsum dolor sit amet, consectetuer adipiscing elit, sed diam nonmmy nibh euismod tincidunt ut laoreet dolore magna aliquam erat volutpat. Ut wisi enim ad minim veniam, quis nostrud exerci tationmcorper suscipit lobortis nisl ut aliquip ex ea commodo consequat. Duis autem vel eum iriure dolor in hendrerit in vulputate velit esse molestie consequat, vel illum dolore eu feugiat nulla facilisis at vero eros et accumsan et iusto odio dignissim qui blandit praesent luptatum zzril delenit augue duis dolore te feugait nulla facilisi.</p>
    <p>Nam liber tempor cum soluta nobis eleifend option congue nihil imprdiet doming id quod mazim placerat facer possim assum. Typi non habent claritatem insitam;</p>
    <p>Est usus legentis in iis qui facit eorum claritatem.</p>
    <p>Investigationes demonstraverunt lectores legere me lius quod ii legunt saepius. Claritas est etiam processus dynamicus, qui sequitur mutationem consuetudium lectorum. Mirum est notare quam littera gothica, quam nunc putamus parum claram, anteposuerit litterarum formas humanitatis per seacula quarta decima et quinta decima. Eodem modo typi, qui nunc nobis videntur parum clari, fiant sollemnes in futurum.</p>
    <p>consectetuer adipiscing elit, sed diam nonummy nibh euismod tincidunt ut laoreet dolore magna aliquam erat volutpat. Ut wisi enim ad minim veniam, quis nostrud exerci tation ullamcorper suscipit lobortis nisl ut aliquip ex ea commodo consequat. Duis autem vel eum iriure dolor in hendrerit in vulputate velit esse molestie consequat, vel illum dolore eu feugiat nulla facilisis at vero eros et accumsan et iusto odio dignissim qui blandit praesent luptatum zzril delenit augue duis dolore te feugait nulla facilisi.</p>
    <p>Nam liber tempor cum soluta nobis eleifend option congue nihil imperdiet .</p>
  </article>

  <div class="signature" role="img" aria-label="Handwritten signature of Peter Hallam"></div>
  <div class="signatory">
    <div class="name">Peter Hallam</div>
    <div class="title">Managing Director</div>
  </div>

  <footer class="footer">
    <div class="contacts">
      <svg viewBox="0 0 24 24" aria-hidden="true"><path fill="var(--red)" d="M6.6 10.8a15 15 0 0 0 6.6 6.6l2.2-2.2c.3-.3.7-.4 1-.2 1.1.4 2.300.6 3.6.6.6 0 1 .4 1 1V20c0 .6-.4 1-1 1A17 17 0 0 1 3 4c0-.6.4-1 1-1h3.5c.6 0 1 .4 1 1 0 1.3.2 2.5.6 3.6.1.3 0 .7-.2 1z"/></svg>
      <span>832-361-9027</span>
      <svg viewBox="0 0 24 24" aria-hidden="true"><path fill="var(--red)" d="M6 3h10l2 2v4H6zM3 10h18v8h-3v3H6v-3H3zm5 6v3h8v-3z"/></svg>
      <span>832-614-7359</span>
    </div>
    <div class="rule"></div>
    <div class="address">1475 Calloway Street, Suite 210, Houston, Texas 77041</div>
  </footer>
</main>
</body>
</html>
```